Varnik Holdings — Business Card Design Brief
Overview
Design a double-sided business card for Varnik Holdings that highlights our two service arms: Varnik Communications (telecommunications) and Varnik Energy (business energy solutions). The card should feel smart and stand out when handed to clients.

Objectives
Showcase our areas of specialty clearly.
Reflect the overall Varnik / Varnik Holdings brand while acknowledging both arms.
Explore using both logos (Communications + Energy) or one unified logo, depending on the design.

Deliverables
One double-sided business card design (front + back).

Content & Copy
Front (preferred): Logo: Varnik / Varnik Holdings
Descriptor: Business Communications | Business Energy
Back:My contact details and company details
Core products: Business Mobile • Telephony • Internet • Business Energy Solutions

Brand & Visual Direction
We have a group logo currently tailored more toward telecoms, plus a separate Varnik Energy logo.
Please explore layouts that use both logos or just one, whichever works best.
Color: I wouldn't mind seeing an option using our the Blue/Purple gradient from our website (varnik-example.co.uk), but also open to non-gradient approaches and other colours..

Overall look: Smart, modern, and distinctive.
Format & Print Specs
Double-sided business card format. (Use a standard size

Must-Haves
Front: Varnik wording or Varnik Holdings wording with atleast 1 logo also on front “Business Communications | Business Energy.”

Back: Contact + company details and core products.
A design that stands out while remaining professional.

Nice-to-Have Options
A gradient version using our site’s Blue/Purple gradient.
A non-gradient version.
A dual-logo treatment versus a single-logo treatment.

Thanks
Owen

```html
<!DOCTYPE html>
<html lang="en">
<head>
<meta charset="utf-8">
<title>Varnik Holdings — Business Card</title>
<link rel="stylesheet" href="https://fonts.googleapis.com/css2?family=Poppins:wght@700&family=Roboto:wght@400;500&display=swap">
<style>
  :root {
    --page-bg: #e6e6e6;
    --card-white: #ffffff;
    --navy: #1d1a6b;
    --green: #3aa629;
    --text-grey: #454545;
    --divider: #9a9a9a;
    --band-blue: #1565d8;
    --band-green: #38a60f;
    --blue-start: #0f60d6;
    --blue-end: #0a98de;
    --green-start: #3cab12;
    --green-end: #b7cd00;
    --white: #ffffff;
  }
  * { box-sizing: border-box; margin: 0; padding: 0; }
  html, body { width: 1200px; height: 1200px; overflow: hidden; }
  body {
    background: var(--page-bg);
    position: relative;
    font-family: "Roboto", Arial, sans-serif;
  }
  .card {
    position: absolute;
    width: 689px;
    height: 394px;
    overflow: hidden;
  }

  /* Contact side */
  .card-contact { left: 267px; top: 159px; background: var(--card-white); }
  .brand-block {
    position: absolute; left: 0; top: 0; width: 323px; height: 358px;
    display: flex; align-items: center; justify-content: center; gap: 14px;
  }
  .brand-dot {
    width: 44px; height: 44px; border-radius: 50%;
    border: 6px solid var(--band-blue);
  }
  .brand-name {
    font-family: "Poppins", sans-serif; font-weight: 700;
    font-size: 36px; color: var(--navy); letter-spacing: 0.5px;
  }
  .divider {
    position: absolute; left: 323px; top: 76px; width: 1px; height: 224px;
    background: var(--divider);
  }
  .contact-block { position: absolute; left: 363px; top: 78px; color: var(--text-grey); }
  .person-name {
    font-family: "Poppins", sans-serif; font-weight: 700;
    font-size: 27px; line-height: 1; color: var(--navy); letter-spacing: 0.5px;
  }
  .person-role { font-size: 16px; color: var(--green); margin-top: 3px; }
  .address { font-size: 16.5px; line-height: 21px; margin-top: 22px; }
  .contact-list { list-style: none; margin-top: 9px; font-size: 16.5px; line-height: 20.5px; }
  .contact-list li { display: flex; align-items: center; gap: 9px; }
  .contact-list svg { width: 14px; height: 14px; fill: var(--navy); flex: none; }
  .website { font-size: 16.5px; margin-top: 14px; }
  .product-band {
    position: absolute; left: 0; bottom: 0; width: 100%; height: 36px;
    display: flex; color: var(--white); font-size: 17.5px;
  }
  .band-comms {
    width: 418px; background: var(--band-blue);
    display: flex; align-items: center; justify-content: center; gap: 18px;
    border-right: 1px solid var(--white);
  }
  .band-energy {
    flex: 1; background: var(--band-green);
    display: flex; align-items: center; justify-content: center;
  }

  /* Brand side */
  .card-brand { left: 262px; top: 654px; display: flex; }
  .brand-half {
    width: 50%; height: 100%; color: var(--white);
    display: flex; flex-direction: column; align-items: center; justify-content: center;
    padding-top: 40px;
  }
  .half-comms { background: linear-gradient(90deg, var(--blue-start), var(--blue-end)); }
  .half-energy { background: linear-gradient(90deg, var(--green-start), var(--green-end)); }
  .half-mark { display: flex; align-items: center; gap: 14px; }
  .half-dot { width: 46px; height: 46px; border-radius: 50%; border: 7px solid var(--white); }
  .half-name {
    font-family: "Poppins", sans-serif; font-weight: 700;
    font-size: 52px; line-height: 1; letter-spacing: 0.5px;
  }
  .half-descriptor { font-size: 17px; margin-top: 26px; }
  .half-energy .half-descriptor { letter-spacing: 3.5px; }
</style>
</head>
<body>

  <section class="card card-contact">
    <div class="brand-block">
      <span class="brand-dot"></span>
      <span class="brand-name">VARNIK</span>
    </div>
    <div class="divider"></div>
    <div class="contact-block">
      <h1 class="person-name">OWEN HALE</h1>
      <p class="person-role">President</p>
      <p class="address">42 Harbour Row<br>Westbridge, UK 210</p>
      <ul class="contact-list">
        <li><svg viewBox="0 0 24 24"><path d="M6.6 10.8a15.1 15.1 0 0 0 6.6 6.6l2.2-2.2a1 1 0 0 1 1-.25 11.4 11.4 0 0 0 3.6.57 1 1 0 0 1 1 1V20a1 1 0 0 1-1 1A17 17 0 0 1 3 4a1 1 0 0 1 1-1h3.5a1 1 0 0 1 1 1c0 1.25.2 2.45.57 3.6a1 1 0 0 1-.25 1z"/></svg>555-210-4817</li>
        <li><svg viewBox="0 0 24 24"><path d="M7 1h10a2 2 0 0 1 2 2v18a2 2 0 0 1-2 2H7a2 2 0 0 1-2-2V3a2 2 0 0 1 2-2zm0 3v15h10V4z"/></svg>555-376-9042</li>
        <li><svg viewBox="0 0 24 24"><path d="M2 5h20v14H2zm2 2v.5l8 5 8-5V7zm0 3v7h16v-7l-8 5z"/></svg>info@varnik-example.co.uk</li>
      </ul>
      <p class="website">www.varnik-example.co.uk</p>
    </div>
    <div class="product-band">
      <div class="band-comms">
        <span>Business Mobile</span><span>•</span><span>Telephony</span><span>•</span><span>Internet</span>
      </div>
      <div class="band-energy">Business Energy Solutions</div>
    </div>
  </section>

  <section class="card card-brand">
    <div class="brand-half half-comms">
      <div class="half-mark">
        <span class="half-dot"></span>
        <span class="half-name">VARNIK</span>
      </div>
      <p class="half-descriptor">BUSINESS COMMUNICATIONS</p>
    </div>
    <div class="brand-half half-energy">
      <div class="half-mark">
        <span class="half-dot"></span>
        <span class="half-name">VARNIK</span>
      </div>
      <p class="half-descriptor">BUSINESS ENERGY</p>
    </div>
  </section>

</body>
</html>
```